Business Card Design for company

We want new business cards. We'd like something different-- yet still highly professional. Our tagline is Providing leadership, delivering success. Stock photos are ok, as long as they are relevant and look upscale.

Target Market(s)

Architecture/Business Management Consulting/Engineering Consulting

Contact Information for Business Card

dark gray background with pops of blue might be good, but you tell me. You're the designers. Rounded corners might be nice, but again, you tell me.

Font styles to use
Serif
Sans Serif

Colors
3276b5
5c5c5c
9d9d9d
fbfbfb

Requirements
Nice to have
• Something different, but still very professional.

```html
<!DOCTYPE html>
<html lang="en">
<head>
<meta charset="utf-8">
<title>Halvern Group — Business Cards</title>
<link rel="stylesheet" href="https://fonts.googleapis.com/css2?family=Open+Sans:wght@400;600&display=swap">
<style>
  :root {
    --blue: #3276b5;
    --blue-light: #5a9ad0;
    --grey-dark: #5c5c5c;
    --grey-mid: #9d9d9d;
    --paper: #fbfbfb;
    --backdrop: #dcdcdc;
  }
  * { margin: 0; padding: 0; box-sizing: border-box; }
  html, body { width: 1200px; height: 864px; overflow: hidden; }
  body {
    background: var(--backdrop);
    font-family: "Open Sans", sans-serif;
    display: flex;
    align-items: center;
    justify-content: center;
    gap: 48px;
  }
  .card {
    position: relative;
    width: 540px;
    height: 310px;
    background: var(--paper);
    box-shadow: 0 6px 18px rgba(0,0,0,0.18);
    overflow: hidden;
  }
  .wordmark {
    color: var(--blue);
    font-weight: 600;
    letter-spacing: 0.5px;
    white-space: nowrap;
  }
  /* Front */
  .card-front .wordmark {
    position: absolute;
    left: 34px;
    top: 38px;
    font-size: 46px;
    line-height: 1;
  }
  .rule {
    position: absolute;
    left: 0;
    width: 100%;
    height: 4px;
    background: var(--grey-dark);
  }
  .rule-top { top: 144px; }
  .rule-bottom { top: 262px; }
  .band {
    position: absolute;
    left: 0;
    top: 154px;
    width: 100%;
    height: 102px;
    background: linear-gradient(100deg, var(--blue) 0%, var(--blue-light) 55%, var(--blue) 100%);
    color: var(--paper);
  }
  .identity {
    position: absolute;
    right: 36px;
    top: 96px;
    text-align: right;
  }
  .identity .name {
    color: var(--blue);
    font-weight: 600;
    font-size: 19px;
    line-height: 1.1;
  }
  .identity .role {
    color: var(--grey-dark);
    font-size: 13px;
  }
  .contacts {
    position: absolute;
    left: 30px;
    top: 14px;
    list-style: none;
    font-size: 13.5px;
    line-height: 24px;
  }
  .contacts li, .address {
    display: flex;
    align-items: flex-start;
    gap: 9px;
  }
  .icon {
    flex: none;
    width: 14px;
    height: 14px;
    margin-top: 5px;
  }
  .address {
    position: absolute;
    left: 300px;
    top: 22px;
    font-size: 13.5px;
    line-height: 20px;
  }
  /* Back */
  .card-back {
    display: flex;
    align-items: center;
    justify-content: center;
  }
  .card-back .wordmark { font-size: 50px; }
</style>
</head>
<body>

<section class="card card-front" aria-label="Business card front">
  <div class="wordmark">Halvern Group</div>

  <div class="identity">
    <div class="name">Daniel Moreau</div>
    <div class="role">Owner</div>
  </div>

  <div class="rule rule-top"></div>
  <div class="band">
    <ul class="contacts">
      <li>
        <svg class="icon" viewBox="0 0 14 14" aria-hidden="true"><rect width="14" height="14" rx="3" fill="#fbfbfb"/><path d="M4.5 3.5c.6-.3 1.1 0 1.3.5l.4 1.2c.1.4-.1.7-.4.9l-.4.3c.3.9 1 1.6 1.9 1.9l.3-.4c.2-.3.6-.4.9-.3l1.2.4c.5.2.8.7.5 1.3-.3.7-1 1.2-1.9 1-2.3-.5-4-2.2-4.5-4.5-.2-.9.3-1.6.7-2.3z" fill="#3276b5"/></svg>
        <span>+0000-0000-0000</span>
      </li>
      <li>
        <svg class="icon" viewBox="0 0 14 14" aria-hidden="true"><rect width="14" height="14" rx="3" fill="#fbfbfb"/><rect x="3" y="4" width="8" height="6" fill="none" stroke="#3276b5" stroke-width="1.2"/><path d="M3 4l4 3.2L11 4" fill="none" stroke="#3276b5" stroke-width="1.2"/></svg>
        <span>info@yourdomain.com</span>
      </li>
      <li>
        <svg class="icon" viewBox="0 0 14 14" aria-hidden="true"><rect width="14" height="14" rx="3" fill="#fbfbfb"/><circle cx="7" cy="7" r="3.8" fill="none" stroke="#3276b5" stroke-width="1.2"/><path d="M3.2 7h7.6M7 3.2c-1.4 1.8-1.4 5.8 0 7.6M7 3.2c1.4 1.8 1.4 5.8 0 7.6" fill="none" stroke="#3276b5" stroke-width="0.9"/></svg>
        <span>www.yourdomain.com</span>
      </li>
    </ul>
    <div class="address">
      <svg class="icon" viewBox="0 0 14 14" aria-hidden="true"><rect width="14" height="14" rx="3" fill="#fbfbfb"/><path d="M7 2.8a3 3 0 0 1 3 3c0 2.2-3 5.4-3 5.4S4 8 4 5.8a3 3 0 0 1 3-3z" fill="#3276b5"/><circle cx="7" cy="5.8" r="1.1" fill="#fbfbfb"/></svg>
      <span>Suite 210,<br>48 Calder Row,<br>London</span>
    </div>
  </div>
  <div class="rule rule-bottom"></div>
</section>

<section class="card card-back" aria-label="Business card back">
  <div class="wordmark">Halvern Group</div>
</section>

</body>
</html>
```